Tallowood building company Business card design

I need a business card design for my company. I have a logo but dont have business cards with our logo..

www.tallowoodbuildingco.com.au

The logo is on the website

I need the same details as this design I have attached. we have changed the logo and colours. just like the website

Building

```html
<!DOCTYPE html>
<html lang="en">
<head>
<meta charset="utf-8">
<title>Tallowood Building – Business Card</title>
<link rel="stylesheet" href="https://fonts.googleapis.com/css2?family=Cinzel:wght@500&family=Lato:wght@400;700&display=swap">
<style>
  :root {
    --blue: #1a8ccc;
    --grey-band: #c3c4c6;
    --ink: #1c1c1c;
    --rule: #b9b9b9;
    --card: #ffffff;
    --backdrop: #ecebe8;
  }
  * { box-sizing: border-box; margin: 0; padding: 0; }
  html, body {
    width: 1200px; height: 830px; overflow: hidden;
    background: var(--backdrop);
  }
  .card {
    position: absolute; left: 150px; top: 158px;
    width: 900px; height: 514px;
    background: var(--card);
    box-shadow: 0 6px 22px rgba(0,0,0,.18);
    overflow: hidden;
  }
  .band-grey {
    position: absolute; left: 0; right: 0; bottom: 42px; height: 70px;
    background: var(--grey-band);
  }
  .band-blue {
    position: absolute; left: 0; right: 0; bottom: 0; height: 42px;
    background: var(--blue);
  }
  .brand {
    position: absolute; left: 40px; top: 120px; width: 390px;
    text-align: center;
  }
  .brand-mark {
    display: inline-block; width: 22px; height: 22px;
    background: var(--blue); margin-bottom: 18px;
  }
  .brand-name {
    font-family: "Lato", sans-serif; font-weight: 700;
    color: var(--blue); font-size: 44px; letter-spacing: 3px;
    text-transform: uppercase; line-height: 1.05;
  }
  .brand-rule {
    height: 2px; background: var(--rule); margin: 18px 10px 12px;
  }
  .tagline {
    font-family: "Lato", sans-serif; font-size: 20px;
    color: var(--ink); line-height: 1.3;
  }
  .divider {
    position: absolute; left: 452px; top: 30px; width: 2px; height: 330px;
    background: linear-gradient(var(--rule), #d8d8d8);
  }
  .person {
    position: absolute; left: 490px; top: 40px;
  }
  .person-name {
    font-family: "Cinzel", serif; font-weight: 500;
    font-size: 25px; color: var(--ink); letter-spacing: 1.5px;
  }
  .person-role {
    font-family: "Lato", sans-serif; font-size: 18px;
    color: var(--blue); letter-spacing: 1px;
    margin-left: 110px; margin-top: 2px;
  }
  .contacts {
    position: absolute; left: 490px; top: 200px;
    list-style: none;
  }
  .contact {
    display: flex; align-items: center; gap: 18px;
    font-family: "Lato", sans-serif; font-size: 21px; color: var(--ink);
    margin-bottom: 16px;
  }
  .contact svg { width: 24px; height: 24px; flex: none; }
</style>
</head>
<body>
  <main class="card">
    <section class="brand">
      <span class="brand-mark"></span>
      <div class="brand-name">Tallowood<br>Building</div>
      <div class="brand-rule"></div>
      <p class="tagline">New Homes, Addition &amp; Renovation<br>Domestic &amp; Commercial Builders</p>
    </section>

    <div class="divider"></div>

    <section class="person">
      <h1 class="person-name">Marin Dobrescu</h1>
      <p class="person-role">Director</p>
    </section>

    <ul class="contacts">
      <li class="contact">
        <svg viewBox="0 0 24 24" aria-hidden="true"><path fill="#1a8ccc" d="M3 9c0-3 4-5 9-5s9 2 9 5v2h-5V9H8v2H3z"/><rect x="6" y="12" width="12" height="8" rx="1.5" fill="#1a8ccc"/></svg>
        9315 2740
      </li>
      <li class="contact">
        <svg viewBox="0 0 24 24" aria-hidden="true"><rect x="6" y="2" width="12" height="20" rx="2.5" fill="none" stroke="#1a8ccc" stroke-width="2"/><circle cx="12" cy="18.5" r="1.2" fill="#1a8ccc"/></svg>
        0412556193 (Marin)
      </li>
      <li class="contact">
        <svg viewBox="0 0 24 24" aria-hidden="true"><rect x="2" y="5" width="20" height="14" rx="1.5" fill="#1a8ccc"/><path d="M2.5 6l9.5 7 9.5-7" fill="none" stroke="#fff" stroke-width="1.5"/></svg>
        info@tallowoodbuildingco.com.au
      </li>
    </ul>

    <div class="band-grey"></div>
    <div class="band-blue"></div>
  </main>
</body>
</html>
```